TALMORK

The business want a professional looking business card. We have a scetch we will add but want the extra upgrade, and would like more suggestions for variations of our business cards.

```html
<!DOCTYPE html>
<html lang="en">
<head>
<meta charset="utf-8">
<title>TALMORK business card</title>
<link rel="stylesheet" href="https://fonts.googleapis.com/css2?family=Arimo:wght@400;500&display=swap">
<style>
  :root {
    --backdrop: #3d3d3d;
    --card-light: #ffffff;
    --card-dark: #2f2f2f;
    --gold: #b48a3c;
    --gold-soft: #c9a35a;
    --ink: #4a4a4a;
    --ink-muted: #6b6b6b;
    --rule: #b5b5b5;
    --tint: #f7f5f0;
  }
  * { margin: 0; padding: 0; box-sizing: border-box; }
  html, body {
    width: 1200px; height: 1200px; overflow: hidden;
    background: var(--backdrop);
    font-family: "Arimo", Arial, sans-serif;
  }
  .canvas { position: relative; width: 1200px; height: 1200px; }
  .card { position: absolute; width: 689px; height: 394px; border-radius: 26px; overflow: hidden; }
  .card--front { left: 266px; top: 158px; background: var(--card-light); }
  .card--back { left: 262px; top: 652px; background: var(--card-dark); }

  .front-tint {
    position: absolute; left: -40px; top: 20px; width: 380px; height: 380px;
    border-radius: 50%; background: var(--tint);
  }

  .brand { position: absolute; text-align: center; color: var(--gold); }
  .brand--front { left: 430px; top: 86px; width: 221px; }
  .brand__dot { display: block; margin: 0 auto; border-radius: 50%; background: var(--gold); }
  .brand--front .brand__dot { width: 40px; height: 40px; margin-bottom: 18px; }
  .brand__name { display: block; font-weight: 500; letter-spacing: 0.2em; }
  .brand--front .brand__name { font-size: 26px; padding-left: 0.2em; }
  .brand__since { display: block; font-size: 8px; letter-spacing: 0.6em; margin-top: 6px; padding-left: 0.6em; }

  .person { position: absolute; left: 47px; top: 244px; }
  .person__name { font-size: 21px; color: var(--gold); font-weight: 400; line-height: 1; }
  .person__role { font-size: 15px; color: var(--ink-muted); margin-top: 8px; line-height: 1; }

  .divider { position: absolute; left: 38px; right: 38px; top: 302px; height: 1px; background: var(--rule); }

  .contact { position: absolute; left: 47px; top: 314px; list-style: none; }
  .contact__item { display: flex; align-items: center; font-size: 17px; color: var(--ink); line-height: 21px; }
  .contact__icon { width: 12px; height: 12px; margin-right: 10px; flex: none; }

  .web { position: absolute; font-size: 16px; letter-spacing: 0.14em; }
  .web--front { right: 38px; top: 335px; color: var(--ink); }
  .web--back { left: 0; right: 0; top: 302px; text-align: center; color: #f2f2f2; }

  .brand--back { left: 0; right: 0; top: 116px; }
  .brand--back .brand__dot { width: 56px; height: 56px; margin-bottom: 22px; }
  .brand--back .brand__name { font-size: 38px; padding-left: 0.2em; }
</style>
</head>
<body>
<main class="canvas">
  <section class="card card--front" aria-label="Card front">
    <div class="front-tint"></div>
    <div class="brand brand--front">
      <span class="brand__dot"></span>
      <span class="brand__name">TALMORK</span>
      <span class="brand__since">SINCE 2026</span>
    </div>
    <div class="person">
      <p class="person__name">Henrik Solberg Aas</p>
      <p class="person__role">CEO &amp; Founder</p>
    </div>
    <div class="divider"></div>
    <ul class="contact">
      <li class="contact__item">
        <svg class="contact__icon" viewBox="0 0 12 12" aria-hidden="true"><rect x="3" y="0.8" width="6" height="10.4" rx="1" fill="none" stroke="var(--gold)" stroke-width="1.3"/><rect x="5" y="9" width="2" height="1" fill="var(--gold)"/></svg>
        004795550142
      </li>
      <li class="contact__item">
        <svg class="contact__icon" viewBox="0 0 12 12" aria-hidden="true"><rect x="1" y="3" width="10" height="7" fill="var(--gold)"/><path d="M1 3 L6 7 L11 3" fill="none" stroke="#fff" stroke-width="1"/></svg>
        talmork.llc@postmail.com
      </li>
    </ul>
    <p class="web web--front">www.talmork.llc</p>
  </section>

  <section class="card card--back" aria-label="Card back">
    <div class="brand brand--back">
      <span class="brand__dot"></span>
      <span class="brand__name">TALMORK</span>
    </div>
    <p class="web web--back">www.talmork.llc</p>
  </section>
</main>
</body>
</html>
```